Plakat-Design 24h Betreuung
Zielgruppe
Wir vermitteln 24h Pflege- und Betreuungskräfte für alte und hilfbedürftige Menschen!
Zielgruppe: deren Angehörige (zwischen 50-70 Jahre alt)
Aufgabenstellung
Klare Ansage - nicht zu verspielt - geradlinig
Maße Plakat: 504 cm breit x 238 cm hoch
Das PLAKAT ist ca 10 m von der Straße entfernet und ist für Autofahrer gedacht - somit muss man alles gut lesen können und groß geschrieben sein !!!!
Folgender Text und Bilder sollte das Plakat beinhalten:
24h - Betreuung (groß links oben platziert)
Logo: SorgeFreund.at
Foto mit 10 Personen
Erfahrung seit 2010
www.sorgefreund.at

```html
<!DOCTYPE html>
<html lang="de">
<head>
<meta charset="utf-8">
<title>24h - Betreuung · SorgeFreund.at</title>
<link rel="stylesheet" href="https://fonts.googleapis.com/css2?family=Montserrat:wght@500;600;700;800&display=swap">
<style>
  :root {
    --frame: #21242f;
    --paper: #ffffff;
    --brand-blue: #2a4180;
    --brand-orange: #d4691e;
    --photo-light: #eef0f5;
    --photo-dark: #5c6a8f;
  }
  * { margin: 0; padding: 0; box-sizing: border-box; }
  html, body {
    width: 1200px; height: 704px; overflow: hidden;
    background: var(--frame);
    font-family: "Montserrat", Arial, sans-serif;
  }
  .poster {
    position: relative; width: 1200px; height: 704px;
    background: var(--frame);
  }
  .poster__board {
    position: absolute; left: 71px; top: 71px;
    width: 1058px; height: 561px;
    background: var(--paper); overflow: hidden;
  }
  .headline {
    position: absolute; left: 37px; top: 26px;
    font-size: 83px; font-weight: 800; letter-spacing: 1px;
    color: var(--brand-blue); line-height: 1; white-space: nowrap;
  }
  .badge {
    position: absolute; left: 820px; top: 18px;
    width: 216px; height: 216px;
  }
  .badge__text {
    position: absolute; inset: 0;
    display: flex; flex-direction: column; align-items: center; justify-content: center;
    color: var(--paper); text-align: center; line-height: 1.05;
    padding-top: 4px;
  }
  .badge__label { font-size: 25px; font-weight: 600; }
  .badge__year { font-size: 49px; font-weight: 800; margin-top: 2px; }
  .team-photo {
    position: absolute; left: 299px; top: 135px;
    width: 476px; height: 352px;
    border-radius: 40px 40px 8px 8px;
    background: linear-gradient(180deg, var(--photo-light) 0%, #c9cfdd 45%, var(--photo-dark) 100%);
  }
  .brand-name {
    position: absolute; left: 51px; top: 423px;
    display: flex; align-items: center; gap: 10px;
    font-size: 24px; font-weight: 700; color: var(--brand-blue);
  }
  .brand-name__dot {
    width: 14px; height: 14px; border-radius: 50%;
    background: var(--brand-orange);
  }
  .footer-band {
    position: absolute; left: 0; bottom: 0; width: 1058px; height: 60px;
  }
  .footer-band svg { position: absolute; inset: 0; }
  .footer-band__location {
    position: absolute; left: 54px; top: 0; height: 60px;
    display: flex; align-items: center;
    font-size: 31px; font-weight: 600; color: var(--paper); white-space: nowrap;
  }
  .footer-band__web {
    position: absolute; right: 25px; top: 0; height: 60px;
    display: flex; align-items: center;
    font-size: 32px; font-weight: 700; color: var(--paper); white-space: nowrap;
  }
</style>
</head>
<body>
<main class="poster">
  <section class="poster__board">
    <h1 class="headline">24h - Betreuung</h1>

    <div class="badge">
      <svg width="216" height="216" viewBox="0 0 216 216" aria-hidden="true">
        <circle cx="108" cy="108" r="108" fill="var(--brand-blue)"/>
        <circle cx="108" cy="108" r="94" fill="none" stroke="var(--paper)" stroke-width="4"/>
      </svg>
      <div class="badge__text">
        <span class="badge__label">Erfahrung<br>seit</span>
        <span class="badge__year">2010</span>
      </div>
    </div>

    <div class="team-photo" role="img" aria-label="Gruppenfoto des Teams: zehn Personen in weißen Blusen und Jeans, vorne eine Frau im blauen Kostüm und ein Mann im dunklen Sakko"></div>

    <div class="brand-name">
      <span class="brand-name__dot"></span>
      <span>SorgeFreund.at</span>
    </div>

    <footer class="footer-band">
      <svg width="1058" height="60" viewBox="0 0 1058 60" aria-hidden="true">
        <polygon points="0,0 634,0 606,60 0,60" fill="var(--brand-blue)"/>
        <polygon points="634,0 1058,0 1058,60 606,60" fill="var(--brand-orange)"/>
      </svg>
      <span class="footer-band__location">Seewinkel am Teich, Marienfeld</span>
      <span class="footer-band__web">www.sorgefreund.at</span>
    </footer>
  </section>
</main>
</body>
</html>
```